CopperWanderer Stretching and Strength

We need a application design for a our first IOS application. the goal of the application is to categorize stretching and strength routines for triathlon.

We would like to see designs that use the color orange.

The design of the application should be compliant with the last version of the IOS Mobile.

For this first design we need the folowing pages:

1- Sign up
2- Log in
3- Home
4- View Exercises
5- Do it
6- Profile

The description of each page is in the attached document.

We need a logo design for the application. The logo should express that mission of the application that is for stretch and strength training for Triathlon.

We will use https://pellavokit.example to develop the application, if you have any experience of the limitation that this technology have it will be a plus.

If you have any question please feel free to contact us.

Reason: We will extend the deadline to be sure that we select the best design from all of you. we will take the final decision next Tuesday.

Target Market(s)

The market for my aplicación is the Running a Triathlon world.

Logo Text

CopperWanderer

Font styles to use
Serif

Colors
f37122
ffffff
dcdcdc

Requirements
Must have
• In some future we will add more features in the menu. We should considere it for the design.
• The designs should include all the screens in the power point.

```html
<!DOCTYPE html>
<html lang="en">
<head>
<meta charset="utf-8">
<title>CopperWanderer – Home</title>
<link href="https://fonts.googleapis.com/css2?family=Roboto:wght@400;500&display=swap" rel="stylesheet">
<style>
  :root {
    --orange: #f37122;
    --orange-light: #f79a5f;
    --page-bg: #d5e3ef;
    --screen-bg: #ececec;
    --card: #ffffff;
    --text: #333333;
    --muted: #777777;
    --rule: #e3e3e3;
    --tag-cyan: #1eb8e0;
    --tag-pink: #c56fd6;
    --tag-violet: #6a4fd8;
  }
  * { box-sizing: border-box; margin: 0; padding: 0; }
  html, body { width: 1200px; height: 1200px; overflow: hidden; }
  body { background: var(--page-bg); font-family: "Roboto", sans-serif; color: var(--text); position: relative; }

  .screen {
    position: absolute; left: 274px; top: 20px;
    width: 552px; height: 982px;
    transform: scale(1.18); transform-origin: top left;
    background: var(--screen-bg); overflow: hidden;
  }
  .abs { position: absolute; }

  .app-bar { position: absolute; left: 0; top: 0; width: 552px; height: 100px; background: var(--orange); color: #fff; }
  .status { position: absolute; top: 10px; left: 6px; right: 8px; height: 22px; font-size: 16px; }
  .status .carrier { position: absolute; left: 0; top: 0; display: flex; align-items: center; gap: 6px; }
  .status .clock { position: absolute; left: 0; right: 0; text-align: center; top: 0; }
  .status .battery { position: absolute; right: 0; top: 0; display: flex; align-items: center; gap: 6px; }
  .app-title { position: absolute; left: 0; right: 0; top: 56px; text-align: center; font-size: 22px; font-weight: 500; letter-spacing: .5px; }
  .menu-icon { position: absolute; left: 12px; top: 61px; }

  .card { position: absolute; left: 13px; width: 524px; background: var(--card); box-shadow: 0 1px 3px rgba(0,0,0,.08); overflow: hidden; }
  .activity-card { top: 116px; height: 294px; }
  .history-card { top: 422px; height: 386px; }
  .sponsor-card { top: 820px; height: 147px; }

  .range-tabs { position: absolute; top: 14px; left: 0; right: 0; display: flex; justify-content: center; gap: 38px; font-size: 15px; color: var(--muted); }
  .range-tabs .active { color: var(--orange); }
  .routine-total { position: absolute; top: 50px; left: 0; right: 0; text-align: center; font-size: 16px; }
  .routine-total em { font-style: normal; color: var(--orange); }

  .pager { position: absolute; top: 384px; width: 46px; height: 46px; border-radius: 50%; background: #e2e2e2; }

  .card-heading { position: absolute; left: 22px; font-size: 18px; font-weight: 500; color: #444; }
  .see-more { position: absolute; right: 23px; top: 17px; font-size: 15px; color: var(--orange); font-weight: 500; }
  .heading-rule { position: absolute; left: 92px; right: 98px; top: 26px; height: 1px; background: var(--rule); }

  .entry { position: absolute; left: 0; width: 524px; height: 142px; border-bottom: 1px solid var(--rule); }
  .entry-thumb { position: absolute; left: 23px; top: 0; width: 81px; height: 76px; }
  .entry-title { position: absolute; left: 120px; top: -3px; font-size: 18px; color: #333; }
  .entry-age { position: absolute; right: 23px; top: 2px; font-size: 12px; color: var(--muted); }
  .tags { position: absolute; left: 120px; top: 25px; display: flex; gap: 6px; }
  .tag { font-size: 10px; color: #fff; border-radius: 8px; padding: 2px 12px; line-height: 12px; }
  .tag.flex { background: var(--tag-cyan); }
  .tag.leg { background: var(--tag-pink); }
  .tag.pain { background: var(--tag-violet); }
  .entry-desc { position: absolute; left: 120px; top: 50px; width: 380px; font-size: 14px; line-height: 22px; color: #555; }
  .entry-meta { position: absolute; left: 120px; top: 97px; font-size: 13px; color: #555; display: flex; gap: 24px; }
  .entry-meta b { font-weight: 400; color: var(--orange); }

  .sponsor-tile { position: absolute; top: 52px; width: 156px; height: 84px; border: 1px solid var(--rule); display: flex; align-items: center; justify-content: center; font-size: 18px; font-weight: 500; color: #222; }
</style>
</head>
<body>
<main class="screen">
  <header class="app-bar">
    <div class="status">
      <span class="carrier">
        <svg width="48" height="10" viewBox="0 0 48 10"><circle cx="5" cy="5" r="4" fill="#fff"/><circle cx="15" cy="5" r="4" fill="#fff"/><circle cx="25" cy="5" r="4" fill="#fff"/><circle cx="35" cy="5" r="3.5" fill="none" stroke="#fff"/><circle cx="45" cy="5" r="3" fill="none" stroke="#fff"/></svg>
        ORBIT
        <svg width="16" height="12" viewBox="0 0 16 12"><path d="M1 4a10 10 0 0 1 14 0M3.5 6.5a6.5 6.5 0 0 1 9 0M6 9a3 3 0 0 1 4 0" stroke="#fff" stroke-width="1.6" fill="none"/></svg>
      </span>
      <span class="clock">4:21 PM</span>
      <span class="battery">
        <svg width="10" height="16" viewBox="0 0 10 16"><path d="M1 4l8 8-4 3V1l4 3-8 8" stroke="#fcc9a5" stroke-width="1.2" fill="none"/></svg>
        100%
        <svg width="34" height="14" viewBox="0 0 34 14"><rect x="0.5" y="0.5" width="30" height="13" rx="3" fill="none" stroke="#fff"/><rect x="2.5" y="2.5" width="26" height="9" rx="1.5" fill="#fff"/><rect x="31.5" y="4.5" width="2" height="5" fill="#fff"/></svg>
      </span>
    </div>
    <svg class="menu-icon" width="26" height="18" viewBox="0 0 26 18"><path d="M0 2h26M0 9h26M0 16h26" stroke="#fff" stroke-width="2"/></svg>
    <h1 class="app-title">HOME</h1>
  </header>

  <section class="card activity-card">
    <nav class="range-tabs"><span class="active">Today</span><span>Yestarday</span><span>This Week</span><span>This Month</span></nav>
    <p class="routine-total">Total Routines: (<em>1</em>/3)</p>
    <svg class="abs" style="left:0;top:0" width="524" height="294" viewBox="0 0 524 294" font-family="Roboto, sans-serif">
      <defs>
        <linearGradient id="barFill" x1="0" y1="0" x2="0" y2="1">
          <stop offset="0" stop-color="#f79a5f"/><stop offset="1" stop-color="#f37122"/>
        </linearGradient>
      </defs>
      <g stroke="#eeeeee">
        <path d="M122 86V253M187 86V253M253 86V253M318 86V253M384 86V253M449 86V253"/>
      </g>
      <path d="M57 86V253H467" stroke="#cccccc" fill="none"/>
      <text transform="translate(50 164) rotate(-90)" font-size="12" fill="#666">Lorem ipsum</text>
      <rect x="101" y="177" width="43" height="76" fill="url(#barFill)"/>
      <rect x="232" y="146" width="43" height="107" fill="url(#barFill)"/>
      <rect x="363" y="208" width="43" height="45" fill="url(#barFill)"/>
      <g font-size="13" fill="#555" text-anchor="middle">
        <text x="122" y="166">Lorem ipsum</text>
        <text x="253" y="134">Lorem ipsum</text>
        <text x="384" y="195">Lorem ipsum</text>
      </g>
      <g font-size="13" fill="#555" text-anchor="middle">
        <text x="56" y="274">10am</text><text x="122" y="274">11am</text><text x="187" y="274">12pm</text>
        <text x="253" y="274">1pm</text><text x="318" y="274">2pm</text><text x="384" y="274">3pm</text><text x="449" y="274">4pm</text>
      </g>
      <circle cx="12" cy="147" r="23" fill="#e2e2e2"/>
      <path d="M17 138l-8 9 8 9" stroke="#999" stroke-width="1.5" fill="none"/>
      <circle cx="510" cy="147" r="23" fill="#e2e2e2"/>
      <path d="M506 138l8 9-8 9" stroke="#333" stroke-width="1.5" fill="none"/>
    </svg>
  </section>

  <section class="card history-card">
    <h2 class="card-heading" style="top:14px">History</h2>
    <div class="heading-rule"></div>
    <a class="see-more">See More</a>

    <article class="entry" style="top:78px">
      <div class="entry-thumb" role="img" aria-label="Photo of a group doing outdoor stretching exercises" style="background:linear-gradient(160deg,#9fb78a,#5e6a58 60%,#3d4a55)"></div>
      <h3 class="entry-title">Lorem ipsum dolor sit amet</h3>
      <span class="entry-age">5 min ago</span>
      <div class="tags"><span class="tag flex">Flexibility</span><span class="tag leg">Leg</span><span class="tag pain">Pain Relief</span></div>
      <p class="entry-desc">Lorem ipsum dolor sit amet, consectetur adipiscing elit. Etiam vitae eros efficitur...</p>
      <p class="entry-meta"><span><b>Time:</b> 5:32 min</span><span><b>Level:</b> Moderate</span></p>
    </article>

    <article class="entry" style="top:220px">
      <div class="entry-thumb" role="img" aria-label="Photo of people doing a yoga stretch on mats" style="background:linear-gradient(160deg,#5a5a6e,#8a4a4a 55%,#b0704a)"></div>
      <h3 class="entry-title">Lorem ipsum dolor sit amet</h3>
      <span class="entry-age">4 h ago</span>
      <div class="tags"><span class="tag flex">Flexibility</span><span class="tag pain">Pain Relief</span></div>
      <p class="entry-desc">Lorem ipsum dolor sit amet, consectetur adipiscing elit. Etiam vitae eros efficitur...</p>
      <p class="entry-meta"><span><b>Time:</b> 4:25 min</span><span><b>Level:</b> Easy</span></p>
    </article>

    <article class="entry" style="top:362px;opacity:.7;border:none">
      <div class="entry-thumb" role="img" aria-label="Photo of a stretching routine" style="background:linear-gradient(90deg,#aaa,#eee)"></div>
      <h3 class="entry-title">Lorem ipsum dolor sit amet</h3>
      <span class="entry-age">6 h ago</span>
    </article>
  </section>

  <section class="card sponsor-card">
    <h2 class="card-heading" style="top:14px">Sponsors</h2>
    <div class="sponsor-tile" style="left:17px">Stridewell</div>
    <div class="sponsor-tile" style="left:181px">Voltmart</div>
    <div class="sponsor-tile" style="left:345px">Harborline Inn</div>
    <div class="sponsor-tile" style="left:509px"></div>
  </section>
</main>
</body>
</html>
```